International professional tennis coach needs a book cover design

This is my 2nd published book, the first one was a #1 on the best seller. I'm looking for a world class book cover design for this new book. The name of my first book was 5 Baseline Habits to Unlock Your Flow Rhythm, located on Bookvale.com

The title of the new book:

Title: The Craft of Rally Mastery
Subtitle: Building a Tactical Match Advantage through Data-Driven Court Insight

I'm uploading our new CRAFT OF RALLY logo that I'd like for you to use as the centerpiece of the book design along with a 21st century design feel that incorporates what the book topic is below::

--> This book is about building competitive intelligence by using tennis data analytics to develop and expand a player's strategic advantage for match play. <--

The colors we would like to use are Blue, Yellow, and Green. These shades of these colors should be bold! (You will see the bold color examples of blues, yellows, and greens that I'm talking about in the logos that are attached here, especially the colors for my Racket GridDrill App logo.

I will upload the Racket GridDrill logo which should go somewhere on the back cover design (small size maybe in the bottom corner).

This book is revolutionary to the standard way of teaching tennis, it is based on a decade of recording and gathering tennis data analytics and then we created on-court practice games to develop better decision making in players for the competitive edge.

My websites are www.elevatedrillzone.com and www.craftofrallymastery.com

```html
<!DOCTYPE html>
<html lang="en">
<head>
<meta charset="utf-8">
<title>The Craft of Rally Mastery — Book Cover</title>
<link rel="stylesheet" href="https://fonts.googleapis.com/css2?family=Bebas+Neue&family=Great+Vibes&family=Montserrat:wght@400&family=Oswald:wght@600&display=swap">
<style>
  :root {
    --backdrop: #c9ced3;
    --paper: #ffffff;
    --leaf-green: #8cc63f;
    --forest-green: #16701a;
    --forest-green-light: #3b8c37;
    --ink: #2b2b2b;
    --court-blue: #0a6cf2;
    --ball-yellow: #f9c80e;
  }
  * { margin: 0; padding: 0; box-sizing: border-box; }
  html, body {
    width: 1200px;
    height: 1200px;
    overflow: hidden;
    background: var(--backdrop);
  }
  .book-cover {
    position: absolute;
    left: 242px;
    top: 50px;
    width: 716px;
    height: 1100px;
    overflow: hidden;
    background: var(--paper);
    box-shadow: 0 10px 30px rgba(0,0,0,0.18);
    display: flex;
    flex-direction: column;
    align-items: center;
  }
  .title {
    margin-top: 44px;
    text-align: center;
    font-weight: normal;
  }
  .title-script {
    display: block;
    font-family: "Great Vibes", cursive;
    font-size: 108px;
    line-height: 1;
    color: var(--leaf-green);
  }
  .title-main {
    display: block;
    margin-top: 8px;
    font-family: "Bebas Neue", sans-serif;
    font-size: 196px;
    line-height: 0.88;
    background: linear-gradient(100deg, var(--forest-green-light), var(--forest-green) 45%);
    -webkit-background-clip: text;
    background-clip: text;
    color: transparent;
    letter-spacing: 1px;
  }
  .series-mark {
    margin-top: 40px;
    height: 220px;
    display: flex;
    align-items: center;
    gap: 18px;
  }
  .series-mark__dot {
    width: 42px;
    height: 42px;
    border-radius: 50%;
    background: var(--ball-yellow);
  }
  .series-mark__name {
    font-family: "Bebas Neue", sans-serif;
    font-size: 64px;
    color: var(--court-blue);
    letter-spacing: 2px;
  }
  .subtitle {
    margin-top: 30px;
    width: 420px;
    padding: 12px 0 14px;
    border-top: 1.5px solid var(--leaf-green);
    border-bottom: 1.5px solid var(--leaf-green);
    font-family: "Montserrat", sans-serif;
    font-size: 20px;
    line-height: 1.4;
    text-align: center;
    color: var(--ink);
    letter-spacing: 0.5px;
  }
  .authors {
    margin-top: 58px;
    font-family: "Oswald", sans-serif;
    font-weight: 600;
    font-size: 40px;
    color: var(--forest-green);
    letter-spacing: 0.5px;
  }
</style>
</head>
<body>
  <main class="book-cover">
    <h1 class="title">
      <span class="title-script">The Craft of</span>
      <span class="title-main">RALLY<br>MASTERY</span>
    </h1>
    <div class="series-mark">
      <span class="series-mark__dot"></span>
      <span class="series-mark__name">CRAFT OF RALLY</span>
    </div>
    <p class="subtitle">Building a Tactical Match Advantage<br>through Data-Driven Court Insight</p>
    <p class="authors">CORWEN HALSTEAD &amp; MILES DRAPER</p>
  </main>
</body>
</html>
```